Candle Rental Business seeks new website design

We need a new website design for a Candle hire business. The business rents out pillar candles for events such as weddings and corporate events. Our main target market is weddings. The business name is Hire a Lantern. The business name does not have a logo design.

We would like a website that is light in colours and creates a warm atmosphere. The design needs to be elegant and upmarket. There are different size candles that we hire out, ranging from 10cm diameter to 20cm diameter, flat, tall etc. All our candles are white in colour. Its just the size that differs.

We would also like to include a section for hiring out decor such as glassvases, candlebras, overlays and chairs sachets, chair covers. However, this is not the businesses main focus but an additional offering to customers.

Target Market(s)

Wedding venues and brides. Corporate events. School dances.

Industry/Entity Type

Hospitality

Logo Text

Hire a Lantern

Number of Pages Required

1 page

Font styles to use
Sans Serif
Script

Requirements
Must have
• Pictures of pillar candles. Plain white candles. The website must centre around candles.
Nice to have
• Different examples of candle centrepieces
Should not have
• Pictures must not be of brides. Pictures of surrounding is perferable.

```html
<!DOCTYPE html>
<html lang="en">
<head>
<meta charset="utf-8">
<title>Hire a Lantern — Candle Hire</title>
<link href="https://fonts.googleapis.com/css2?family=Raleway:wght@400;500;600;700&family=Open+Sans:wght@400;600;700&display=swap" rel="stylesheet">
<style>
:root{
  --red:#d2151c;
  --nav-red:#f5133b;
  --orange:#f5a21a;
  --ink:#222;
  --muted:#777;
  --line:#dcdcdc;
  --panel:#f2f2f2;
  --card-grey:#8f8f8f;
  --footer:#111;
  --footer-bar:#0a0a0a;
  --social-1:#2270cf;
  --social-2:#1ba8e0;
  --social-3:#1d4f66;
  --social-4:#e12b36;
}
*{box-sizing:border-box;margin:0;padding:0}
html,body{width:1200px;height:3488px;overflow:hidden;background:#fff}
body{font-family:"Open Sans",Arial,sans-serif;color:var(--ink);position:relative}
.abs{position:absolute}
a{color:inherit;text-decoration:none}

/* header */
.site-header{position:absolute;left:0;top:0;width:1200px;height:142px}
.brand{position:absolute;left:33px;top:42px;display:flex;align-items:center;gap:12px}
.brand-mark{width:34px;height:34px;background:var(--red);border-radius:50%}
.brand-name{font-family:"Raleway",sans-serif;font-weight:700;font-size:26px;color:var(--ink)}
.search{position:absolute;left:391px;top:63px;display:flex;height:35px}
.search-input{width:374px;border:1px solid var(--line);font-size:11px;color:#aaa;padding:0 14px;line-height:33px}
.search-btn{width:75px;background:var(--red);color:#fff;font-size:11px;font-weight:700;text-align:center;line-height:35px}
.top-links{position:absolute;right:45px;top:9px;font-size:11px;color:#666;display:flex;gap:10px}
.top-links .login{color:var(--red)}
.top-links span.sep{color:#ccc}
.cart{position:absolute;left:988px;top:71px;font-size:11px;color:#444;display:flex;align-items:center;gap:10px}
.cart-count{border-left:1px solid var(--line);padding-left:12px}

/* nav */
.main-nav{position:absolute;left:0;top:142px;width:1200px;height:51px;background:var(--nav-red)}
.main-nav ul{list-style:none;display:flex;position:absolute;left:49px;top:0;height:51px;align-items:center}
.main-nav li{color:#fff;font-size:11px;font-weight:600;padding:0 19px;height:51px;line-height:51px}
.main-nav li.home{background:rgba(0,0,0,.12);padding:0 22px;display:flex;align-items:center}
.checkout{position:absolute;left:1047px;top:0;width:107px;height:51px;background:var(--orange);color:#fff;font-size:11px;font-weight:700;display:flex;align-items:center;justify-content:center;gap:8px}

/* hero */
.hero{position:absolute;left:0;top:195px;width:1200px;height:645px;background:linear-gradient(90deg,#cfcfd1 0%,#b9b9bc 45%,#6f6660 70%,#2b211b 100%);overflow:hidden}
.hero-glow{position:absolute;left:760px;top:0;width:440px;height:645px;background:radial-gradient(ellipse at 55% 35%,#f4c15a 0%,rgba(240,170,60,.55) 18%,rgba(60,40,30,0) 55%)}
.hero-title{position:absolute;left:49px;top:208px;font-family:"Raleway",sans-serif;font-weight:500;font-size:60px;color:var(--red);letter-spacing:1px}
.hero-sub{position:absolute;left:49px;top:276px;font-family:"Raleway",sans-serif;font-weight:500;font-size:44px;color:#222}
.hero-text{position:absolute;left:49px;top:342px;width:740px;font-size:13px;line-height:23px;color:#222}
.btn-red{background:var(--red);color:#fff;font-size:13px;font-weight:700;text-align:center}
.hero-btn{position:absolute;left:49px;top:428px;width:153px;height:61px;line-height:61px}
.hero-dots{position:absolute;left:489px;top:567px;display:flex;gap:8px}
.hero-dots i{width:14px;height:14px;border-radius:50%;border:2px solid var(--red);display:block}
.hero-dots i.on{background:var(--red)}

/* promos */
.promo-red{position:absolute;left:49px;top:856px;width:428px;height:395px;background:var(--red);color:#fff;text-align:center}
.promo-red h2{font-family:"Raleway",sans-serif;font-weight:600;font-size:52px;line-height:56px;margin-top:48px}
.promo-red p{font-size:13px;line-height:19px;width:330px;margin:22px auto 0}
.promo-red .btn-white{display:block;width:153px;height:50px;line-height:50px;margin:40px auto 0;background:#fff;color:var(--red);font-size:13px;font-weight:700}
.promo-grey{position:absolute;left:500px;top:856px;width:658px;height:395px;border:2px solid #e7a0a5}
.promo-grey-inner{position:absolute;left:12px;top:8px;width:632px;height:375px;background:var(--card-grey)}
.promo-photo{position:absolute;left:20px;top:40px;width:210px;height:300px;background:linear-gradient(180deg,#9a9a9a 0%,#f1f1f1 35%,#e6e6e6 75%,#a6a6a6 100%);border-radius:6px}
.promo-grey h2{position:absolute;left:240px;top:72px;font-family:"Raleway",sans-serif;font-weight:600;font-size:38px;color:#fff}
.promo-grey h3{position:absolute;left:240px;top:122px;font-family:"Raleway",sans-serif;font-weight:600;font-size:38px;color:var(--red)}
.promo-grey p{position:absolute;left:240px;top:188px;width:360px;font-size:13px;line-height:19px;color:#fff}
.promo-grey .btn-red{position:absolute;left:240px;top:260px;width:153px;height:50px;line-height:50px}

/* top 10 */
.top-models{position:absolute;left:0;top:1286px;width:1200px;height:412px;background:linear-gradient(90deg,#e9e7e6 0%,#f2eeee 30%,#ece4e8 55%,#e3ecef 80%,#eeeeee 100%)}
.section-title{font-family:"Raleway",sans-serif;font-weight:500;color:#111;text-align:center}
.top-models .section-title{position:absolute;left:0;width:1200px;top:36px;font-size:44px}
.section-title em{font-style:normal;color:var(--red)}
.title-rule{position:absolute;top:64px;height:1px;background:#bbb}
.model-card{position:absolute;top:110px;width:193px;height:265px;background:rgba(255,255,255,.35);border:1px solid #c9c9c9;text-align:center}
.model-photo{width:150px;height:130px;margin:22px auto 0;border-radius:8px}
.model-card .name{font-size:13px;font-weight:700;margin-top:36px}
.model-card .price{font-size:13px;color:var(--red);margin-top:4px}
.carousel-arrow{position:absolute;top:228px}

/* new products */
.new-products{position:absolute;left:0;top:1698px;width:1200px;height:652px;background:var(--panel)}
.block-head{position:absolute;left:49px;top:30px;font-family:"Raleway",sans-serif;font-weight:600;font-size:22px;color:#111}
.block-head em{font-style:normal;color:var(--red)}
.head-rule{position:absolute;left:49px;top:66px;width:1105px;height:1px;background:var(--line)}
.filters{position:absolute;right:46px;top:36px;display:flex;gap:7px}
.filters span{border:1px solid #ccc;background:#fff;font-size:9px;padding:2px 8px;color:#555}
.filters span.price{color:var(--red)}
.product{position:absolute;top:105px;width:252px;height:458px;background:#fff}
.product-photo{width:180px;height:200px;margin:28px auto 0;border-radius:6px}
.tag-new{position:absolute;right:24px;top:12px;background:var(--red);color:#fff;font-size:10px;padding:1px 8px}
.product .price{position:absolute;left:16px;top:240px;font-family:"Raleway",sans-serif;font-size:42px;font-weight:500;color:#111}
.product .price s{font-size:18px;color:#777;margin-left:6px}
.product .pname{position:absolute;left:16px;top:296px;font-size:15px;font-weight:600}
.product .pdesc{position:absolute;left:16px;top:322px;width:220px;font-size:13px;line-height:20px;color:#555}
.product .cart-btn{position:absolute;left:16px;top:380px;width:55px;height:52px;background:var(--red);display:flex;align-items:center;justify-content:center}
.product .more{position:absolute;left:95px;top:380px;width:110px;height:52px;background:#e6e6e6;border:1px solid #d0d0d0;color:#555;font-size:14px;text-align:center;line-height:50px}
.pager{position:absolute;left:962px;top:598px;display:flex;gap:5px;align-items:center;font-size:14px}
.pager span{display:inline-block;height:28px;line-height:28px;text-align:center;color:#fff}
.pager .p1{width:28px;background:var(--red)}
.pager .p2{width:28px;background:#777}
.pager .dots{color:#555;width:75px;letter-spacing:2px}
.pager .next{width:60px;background:#777}

/* decor */
.decor{position:absolute;left:0;top:2350px;width:1200px;height:418px}
.decor .section-title{position:absolute;left:0;width:1200px;top:34px;font-size:22px;font-weight:600}
.decor .title-rule{top:48px}
.decor-item{position:absolute;top:116px;width:270px}
.decor-frame{position:relative;height:214px;border:1px solid #ccc;background:#fff}
.decor-photo{position:absolute;left:22px;top:24px;width:186px;height:170px;border-radius:6px}
.decor-tools{position:absolute;right:0;top:0;width:32px;height:212px;border-left:1px solid #ddd;display:flex;flex-direction:column}
.decor-tools span{flex:1;border-bottom:1px solid #ddd;display:flex;align-items:center;justify-content:center}
.decor-tools span:last-child{border-bottom:0}
.decor-tools span.on{background:var(--red)}
.quick-view{position:absolute;right:32px;top:0;background:var(--red);color:#fff;font-size:10px;font-weight:700;padding:0 8px;height:53px;line-height:36px}
.stars{position:absolute;left:10px;top:6px;color:var(--red);font-size:13px;letter-spacing:1px}
.stars b{color:#bbb;font-weight:400}
.decor-item .dname{font-size:17px;margin-top:10px}
.decor-item .dprice{font-size:14px;font-weight:700;color:var(--red);margin-top:1px}

/* social */
.social{position:absolute;left:0;top:2768px;width:1200px;height:232px;background:#f0f0f0}
.social h3{position:absolute;left:0;width:1200px;top:44px;text-align:center;font-family:"Raleway",sans-serif;font-weight:600;font-size:21px;color:#111}
.social-btn{position:absolute;top:109px;width:216px;height:51px;color:#fff;font-weight:700;font-size:18px;display:flex;align-items:center;justify-content:center;gap:12px}
.social-btn i{width:10px;height:10px;background:#fff;display:block}
.social-count{position:absolute;top:173px;width:216px;text-align:center;font-size:12px;color:#666}

/* promises */
.promises{position:absolute;left:0;top:3000px;width:1200px;height:140px;background:var(--red);display:flex}
.promise{flex:1;display:flex;align-items:center;padding-left:84px;gap:24px;color:#fff;font-size:15px;font-weight:700;line-height:19px;border-right:1px solid rgba(255,255,255,.25)}
.promise:last-child{border-right:0}

/* footer */
.site-footer{position:absolute;left:0;top:3140px;width:1200px;height:275px;background:var(--footer);color:#aaa}
.footer-col{position:absolute;top:66px}
.footer-col h4{color:#fff;font-size:12px;font-weight:600;margin-bottom:22px}
.footer-col li{list-style:none;font-size:11px;line-height:22px}
.contact-line{display:flex;gap:14px;font-size:11px;line-height:18px;margin-bottom:16px}
.footer-bar{position:absolute;left:0;top:3415px;width:1200px;height:73px;background:var(--footer-bar);color:#999;font-size:11px}
.footer-bar p{position:absolute;left:67px;top:28px}
.pay-cards{position:absolute;left:1008px;top:24px;display:flex;gap:8px}
.pay-cards i{width:46px;height:28px;background:#fff;border-radius:3px;display:block}
.pay-cards i:nth-child(2){background:#e8e8e8}
.pay-cards i:nth-child(3){background:#2a63b0}
</style>
</head>
<body>

<header class="site-header">
  <div class="brand"><span class="brand-mark"></span><span class="brand-name">Hire a Lantern</span></div>
  <div class="search"><div class="search-input">Enter keyword</div><div class="search-btn">SEARCH</div></div>
  <div class="top-links"><a class="login">LOGIN/REGISTER</a><span class="sep">|</span><a>MY ACCOUNT</a><span class="sep">|</span><a>WISHLIST - 0</a></div>
  <div class="cart">
    <svg width="16" height="14" viewBox="0 0 16 14"><path d="M0 1h3l2 8h8l2-6H4" fill="none" stroke="#444" stroke-width="1.5"/><circle cx="6" cy="12" r="1.4" fill="#444"/><circle cx="12" cy="12" r="1.4" fill="#444"/></svg>
    <span>CART :</span><span class="cart-count">0 (Items)</span>
    <svg width="10" height="6" viewBox="0 0 10 6"><path d="M0 0h10L5 6z" fill="#444"/></svg>
  </div>
</header>

<nav class="main-nav">
  <ul>
    <li class="home"><svg width="18" height="16" viewBox="0 0 18 16"><path d="M9 0L0 8h3v8h4v-5h4v5h4V8h3z" fill="#fff"/></svg></li>
    <li>ABOUT</li><li>NEW PRODUCT</li><li>SPECIAL CANDLE</li><li>FAQS</li><li>ACCESSORIES</li><li>REVIEWS</li><li>PILLAR CANDLES</li><li>CONTACT US</li>
  </ul>
  <div class="checkout">CHECKOUT <svg width="14" height="12" viewBox="0 0 14 12"><path d="M0 4h7V0l7 6-7 6V8H0z" fill="#fff"/></svg></div>
</nav>

<section class="hero">
  <div class="hero-glow" role="img" aria-label="Lit white pillar candle glowing on a soft grey surface"></div>
  <h1 class="hero-title">LATEST MODEL DESIGN</h1>
  <p class="hero-sub">25% OFF FOR CANDLE</p>
  <p class="hero-text">Lorem ipsum dolor sit amet, consectetur adipiscing elit, sed do eiusmod tempor incididunt ut labore et dolore magna aliqua. Lorem ipsum dolor sit amet, consectetur adipiscing elit, sed do eiusmod tempor incididunt ut labore et dolore magna aliqua. Lorem ipsum dolor sit amet, consectetur adipiscing elit, sed do eiusmod tempor.</p>
  <a class="btn-red hero-btn">SHOP NOW</a>
  <div class="hero-dots"><i class="on"></i><i></i><i></i><i></i></div>
</section>

<section class="promo-red">
  <h2>NEW<br>ARRIVALS</h2>
  <p>Lorem ipsum dolor sit amet conse ctetur adipiscing elit, sed do eiusmod tempor incididunt ut labore et dolore magna aliqua.</p>
  <a class="btn-white">SHOP NOW</a>
</section>

<section class="promo-grey">
  <div class="promo-grey-inner">
    <div class="promo-photo" role="img" aria-label="White pillar candle on a glass holder"></div>
    <h2>LATEST PRODUCT</h2>
    <h3>25% OFF</h3>
    <p>Lorem ipsum dolor sit amet conse ctetur adipiscing elit, sed do eiusmod tempor incididunt ut labore et dolore magna aliqua.</p>
    <a class="btn-red">SHOP NOW</a>
  </div>
</section>

<section class="top-models" role="img" aria-label="Soft background of flowers and shells">
  <div class="title-rule" style="left:79px;width:255px"></div>
  <div class="title-rule" style="left:866px;width:255px"></div>
  <h2 class="section-title">Top 10 <em>Model Candles</em></h2>
  <svg class="carousel-arrow" style="left:30px" width="16" height="22" viewBox="0 0 16 22"><path d="M16 0v22L0 11z" fill="#fff"/></svg>
  <svg class="carousel-arrow" style="left:1142px" width="16" height="22" viewBox="0 0 16 22"><path d="M0 0v22l16-11z" fill="#fff"/></svg>
  <div class="model-card" style="left:79px"><div class="model-photo" role="img" aria-label="Pink glass hanging candle holder" style="background:linear-gradient(180deg,#f3eef2,#b9577e 70%,#e8dde4)"></div><p class="name">Product Name</p><p class="price">$ 127.00</p></div>
  <div class="model-card" style="left:291px"><div class="model-photo" role="img" aria-label="Glass hurricane candle holder with roses" style="background:linear-gradient(180deg,#e6e4df,#b7a48e 60%,#d9c7b6)"></div><p class="name">Product Name</p><p class="price">$ 147.00</p></div>
  <div class="model-card" style="left:507px"><div class="model-photo" role="img" aria-label="White pillar candle on glass holder" style="background:linear-gradient(180deg,#f1f1f1,#e4e4e4 60%,#bdbdbd)"></div><p class="name">Product Name</p><p class="price">$ 227.00</p></div>
  <div class="model-card" style="left:735px"><div class="model-photo" role="img" aria-label="Two red glass tealight holders" style="background:linear-gradient(180deg,#efe9e9,#b22a2a 60%,#e3d6d6)"></div><p class="name">Product Name</p><p class="price">$ 27.00</p></div>
  <div class="model-card" style="left:933px"><div class="model-photo" role="img" aria-label="Silver bowl candle" style="background:linear-gradient(180deg,#eeeeee,#c9a46a 45%,#8a8a8a)"></div><p class="name">Product Name</p><p class="price">$ 107.00</p></div>
</section>

<section class="new-products">
  <h2 class="block-head"><em>NEW</em> PRODUCT</h2>
  <div class="filters"><span class="price">PRICE ⌄</span><span>CATEGORY ⌄</span><span>BRAND ⌄</span></div>
  <div class="head-rule"></div>

  <article class="product" style="left:49px">
    <span class="tag-new">New</span>
    <div class="product-photo" role="img" aria-label="Cream candles on a metal stand" style="background:linear-gradient(180deg,#fff,#efe1cc 40%,#d9c3a3)"></div>
    <p class="price">$ 220<s>$275.00</s></p><p class="pname">NAME OF PRODUCT</p>
    <p class="pdesc">Lorem ipsum dolor sit amet, edit consectetur adipiscing elit,</p>
    <a class="cart-btn"><svg width="22" height="20" viewBox="0 0 16 14"><path d="M0 1h3l2 8h8l2-6H4z" fill="#fff"/><circle cx="6" cy="12" r="1.5" fill="#fff"/><circle cx="12" cy="12" r="1.5" fill="#fff"/></svg></a><a class="more">MORE</a>
  </article>
  <article class="product" style="left:333px">
    <div class="product-photo" role="img" aria-label="Set of white flameless pillar candles" style="background:linear-gradient(180deg,#fff,#eeeeee 40%,#d8d8d8)"></div>
    <p class="price">$ 300<s>$325.00</s></p><p class="pname">NAME OF PRODUCT</p>
    <p class="pdesc">Lorem ipsum dolor sit amet, edit consectetur adipiscing elit,</p>
    <a class="cart-btn"><svg width="22" height="20" viewBox="0 0 16 14"><path d="M0 1h3l2 8h8l2-6H4z" fill="#fff"/><circle cx="6" cy="12" r="1.5" fill="#fff"/><circle cx="12" cy="12" r="1.5" fill="#fff"/></svg></a><a class="more">MORE</a>
  </article>
  <article class="product" style="left:616px">
    <span class="tag-new">New</span>
    <div class="product-photo" role="img" aria-label="Lit candle in a brass holder" style="background:linear-gradient(180deg,#fff,#e9c36d 35%,#6b5220 80%,#fff)"></div>
    <p class="price">$ 200<s>$225.00</s></p><p class="pname">NAME OF PRODUCT</p>
    <p class="pdesc">Lorem ipsum dolor sit amet, edit consectetur adipiscing elit,</p>
    <a class="cart-btn"><svg width="22" height="20" viewBox="0 0 16 14"><path d="M0 1h3l2 8h8l2-6H4z" fill="#fff"/><circle cx="6" cy="12" r="1.5" fill="#fff"/><circle cx="12" cy="12" r="1.5" fill="#fff"/></svg></a><a class="more">MORE</a>
  </article>
  <article class="product" style="left:902px">
    <div class="product-photo" role="img" aria-label="Three pillar candles on bronze stands" style="background:linear-gradient(180deg,#fff,#efe9dc 30%,#9c8160 80%,#fff)"></div>
    <p class="price">$ 160<s>$205.00</s></p><p class="pname">NAME OF PRODUCT</p>
    <p class="pdesc">Lorem ipsum dolor sit amet, edit consectetur adipiscing elit,</p>
    <a class="cart-btn"><svg width="22" height="20" viewBox="0 0 16 14"><path d="M0 1h3l2 8h8l2-6H4z" fill="#fff"/><circle cx="6" cy="12" r="1.5" fill="#fff"/><circle cx="12" cy="12" r="1.5" fill="#fff"/></svg></a><a class="more">MORE</a>
  </article>

  <div class="pager"><span class="p1">1</span><span class="p2">2</span><span class="dots">.........</span><span class="next">Next</span></div>
</section>

<section class="decor">
  <div class="title-rule" style="left:49px;width:405px"></div>
  <div class="title-rule" style="left:746px;width:408px"></div>
  <h2 class="section-title"><em>OUT DECOR</em> PRODUCT</h2>

  <div class="decor-item" style="left:49px">
    <div class="decor-frame">
      <div class="decor-photo" role="img" aria-label="Tall clear glass vases" style="background:linear-gradient(180deg,#fff,#eaeaea 50%,#cfcfcf)"></div>
      <span class="stars">★★★★<b>★</b></span>
      <span class="quick-view">Quick View</span>
      <div class="decor-tools">
        <span class="on"><svg width="14" height="10" viewBox="0 0 14 10"><ellipse cx="7" cy="5" rx="6.5" ry="4.2" fill="none" stroke="#fff" stroke-width="1.4"/><circle cx="7" cy="5" r="1.8" fill="#fff"/></svg></span>
        <span><svg width="10" height="10" viewBox="0 0 10 10"><path d="M1 2h6l2 4H3z" fill="#888"/></svg></span>
        <span><svg width="4" height="10" viewBox="0 0 4 10"><rect x="1" y="0" width="2" height="2" fill="#888"/><rect x="1" y="4" width="2" height="6" fill="#888"/></svg></span>
        <span><svg width="10" height="10" viewBox="0 0 10 10"><rect x="0" y="6" width="2" height="4" fill="#888"/><rect x="4" y="3" width="2" height="7" fill="#888"/><rect x="8" y="0" width="2" height="10" fill="#888"/></svg></span>
        <span><svg width="12" height="10" viewBox="0 0 12 10"><path d="M6 10L1 5a2.6 2.6 0 014-3.5L6 2.5l1-1A2.6 2.6 0 0111 5z" fill="none" stroke="#888" stroke-width="1.2"/></svg></span>
      </div>
    </div>
    <p class="dname">Glassvases</p><p class="dprice">$ 33.5</p>
  </div>

  <div class="decor-item" style="left:326px">
    <div class="decor-frame">
      <div class="decor-photo" role="img" aria-label="Bronze candelabra with cream candles" style="background:linear-gradient(180deg,#fff,#efe6d3 35%,#8c7552 80%,#fff)"></div>
      <div class="decor-tools">
        <span><svg width="14" height="10" viewBox="0 0 14 10"><ellipse cx="7" cy="5" rx="6.5" ry="4.2" fill="none" stroke="#888" stroke-width="1.4"/><circle cx="7" cy="5" r="1.8" fill="#888"/></svg></span>
        <span><svg width="10" height="10" viewBox="0 0 10 10"><path d="M1 2h6l2 4H3z" fill="#888"/></svg></span>
        <span><svg width="4" height="10" viewBox="0 0 4 10"><rect x="1" y="0" width="2" height="2" fill="#888"/><rect x="1" y="4" width="2" height="6" fill="#888"/></svg></span>
        <span><svg width="10" height="10" viewBox="0 0 10 10"><rect x="0" y="6" width="2" height="4" fill="#888"/><rect x="4" y="3" width="2" height="7" fill="#888"/><rect x="8" y="0" width="2" height="10" fill="#888"/></svg></span>
        <span><svg width="12" height="10" viewBox="0 0 12 10"><path d="M6 10L1 5a2.6 2.6 0 014-3.5L6 2.5l1-1A2.6 2.6 0 0111 5z" fill="none" stroke="#888" stroke-width="1.2"/></svg></span>
      </div>
    </div>
    <p class="dname">Candlebras</p><p class="dprice">$ 33.5</p>
  </div>

  <div class="decor-item" style="left:605px">
    <div class="decor-frame">
      <div class="decor-photo" role="img" aria-label="Blue organza chair sash on a white chair" style="background:linear-gradient(180deg,#fff,#3d8fd6 40%,#eef3f8 85%)"></div>
      <div class="decor-tools">
        <span><svg width="14" height="10" viewBox="0 0 14 10"><ellipse cx="7" cy="5" rx="6.5" ry="4.2" fill="none" stroke="#888" stroke-width="1.4"/><circle cx="7" cy="5" r="1.8" fill="#888"/></svg></span>
        <span><svg width="10" height="10" viewBox="0 0 10 10"><path d="M1 2h6l2 4H3z" fill="#888"/></svg></span>
        <span><svg width="4" height="10" viewBox="0 0 4 10"><rect x="1" y="0" width="2" height="2" fill="#888"/><rect x="1" y="4" width="2" height="6" fill="#888"/></svg></span>
        <span><svg width="10" height="10" viewBox="0 0 10 10"><rect x="0" y="6" width="2" height="4" fill="#888"/><rect x="4" y="3" width="2" height="7" fill="#888"/><rect x="8" y="0" width="2" height="10" fill="#888"/></svg></span>
        <span><svg width="12" height="10" viewBox="0 0 12 10"><path d="M6 10L1 5a2.6 2.6 0 014-3.5L6 2.5l1-1A2.6 2.6 0 0111 5z" fill="none" stroke="#888" stroke-width="1.2"/></svg></span>
      </div>
    </div>
    <p class="dname">Chairs Sachets</p><p class="dprice">$ 33.5</p>
  </div>

  <div class="decor-item" style="left:884px">
    <div class="decor-frame">
      <div class="decor-photo" role="img" aria-label="White chair cover with purple sash" style="background:linear-gradient(180deg,#fff,#eeeef3 35%,#5a4f9c 60%,#f0f0f4)"></div>
      <div class="decor-tools">
        <span><svg width="14" height="10" viewBox="0 0 14 10"><ellipse cx="7" cy="5" rx="6.5" ry="4.2" fill="none" stroke="#888" stroke-width="1.4"/><circle cx="7" cy="5" r="1.8" fill="#888"/></svg></span>
        <span><svg width="10" height="10" viewBox="0 0 10 10"><path d="M1 2h6l2 4H3z" fill="#888"/></svg></span>
        <span><svg width="4" height="10" viewBox="0 0 4 10"><rect x="1" y="0" width="2" height="2" fill="#888"/><rect x="1" y="4" width="2" height="6" fill="#888"/></svg></span>
        <span><svg width="10" height="10" viewBox="0 0 10 10"><rect x="0" y="6" width="2" height="4" fill="#888"/><rect x="4" y="3" width="2" height="7" fill="#888"/><rect x="8" y="0" width="2" height="10" fill="#888"/></svg></span>
        <span><svg width="12" height="10" viewBox="0 0 12 10"><path d="M6 10L1 5a2.6 2.6 0 014-3.5L6 2.5l1-1A2.6 2.6 0 0111 5z" fill="none" stroke="#888" stroke-width="1.2"/></svg></span>
      </div>
    </div>
    <p class="dname">Chair Covers</p><p class="dprice">$ 33.5</p>
  </div>
</section>

<section class="social">
  <h3>FOLLOW US TO STAY IN TOUCH</h3>
  <a class="social-btn" style="left:109px;background:var(--social-1)"><i></i>Circlebook</a>
  <a class="social-btn" style="left:381px;background:var(--social-2)"><i></i>Chirper</a>
  <a class="social-btn" style="left:640px;background:var(--social-3)"><i></i>Worklink</a>
  <a class="social-btn" style="left:902px;background:var(--social-4)"><i></i>Gatherplus</a>
  <p class="social-count" style="left:109px">1234 Like</p>
  <p class="social-count" style="left:381px">1234 Followers</p>
  <p class="social-count" style="left:640px">1234 Connections</p>
  <p class="social-count" style="left:902px">123 Connections</p>
</section>

<section class="promises">
  <div class="promise">
    <svg width="40" height="38" viewBox="0 0 40 38"><path d="M2 16h8v20H2zM13 16l8-14c4 0 5 3 4 7l-2 6h12c3 0 4 3 3 5l-4 13c-1 2-2 3-4 3H13z" fill="none" stroke="#fff" stroke-width="2.5" stroke-linejoin="round"/></svg>
    <span>SATISFACTION<br>100% GUARANTEED</span>
  </div>
  <div class="promise">
    <svg width="46" height="34" viewBox="0 0 46 34"><path d="M0 2h28v22H0zM28 10h10l8 8v6H28z" fill="#fff"/><circle cx="9" cy="28" r="5" fill="#fff" stroke="var(--red)" stroke-width="2"/><circle cx="37" cy="28" r="5" fill="#fff" stroke="var(--red)" stroke-width="2"/></svg>
    <span>FREE SHIPPING<br>ON ORDERS OVER $99</span>
  </div>
  <div class="promise">
    <svg width="38" height="38" viewBox="0 0 38 38"><path d="M32 12A15 15 0 006 10M6 26a15 15 0 0026 2" fill="none" stroke="#fff" stroke-width="4"/><path d="M2 2v12h12zM36 36V24H24z" fill="#fff"/></svg>
    <span>NEW OFFER<br>ON ORDERS $1000</span>
  </div>
</section>

<footer class="site-footer">
  <div class="footer-col" style="left:67px"><h4>INFORMATION</h4><ul><li>ABOUT US</li><li>CUSTOMER SERVICE</li><li>PRIVACY POLICY</li><li>SEARCH TERMS</li><li>ORDERS AND RETURNS</li><li>CONTACT US</li></ul></div>
  <div class="footer-col" style="left:337px"><h4>WHY BUY FROM US</h4><ul><li>SHIPPING &amp; RETURNS</li><li>SECURE SHOPPING</li><li>INTERNATIONAL SHIPPING</li><li>AFFILIATES</li><li>GROUP SALES</li></ul></div>
  <div class="footer-col" style="left:640px"><h4>MY ACCOUNT</h4><ul><li>SIGN IN</li><li>VIEW CART</li><li>MY WISHLIST</li><li>TRACK MY ORDER</li><li>HELP</li></ul></div>
  <div class="footer-col" style="left:884px"><h4>CONTACTS</h4>
    <div class="contact-line"><svg width="12" height="16" viewBox="0 0 12 16"><path d="M6 0a6 6 0 00-6 6c0 4 6 10 6 10s6-6 6-10a6 6 0 00-6-6z" fill="#aaa"/><circle cx="6" cy="6" r="2" fill="#111"/></svg><span>12 WICKMOOR LANE, ASHFORD AF2 7LN<br>P. O BOX 40817, COUNTRY.</span></div>
    <div class="contact-line"><svg width="12" height="14" viewBox="0 0 12 14"><path d="M2 0h3l1 4-2 1c1 2 2 4 4 5l1-2 3 1v3c0 1-1 2-2 2C5 14 0 9 0 2c0-1 1-2 2-2z" fill="#aaa"/></svg><span>CALL US: (555) 0142-3876</span></div>
    <div class="contact-line"><svg width="14" height="10" viewBox="0 0 14 10"><rect width="14" height="10" fill="#aaa"/><path d="M0 0l7 6 7-6" fill="none" stroke="#111" stroke-width="1.2"/></svg><span>EMAIL: HELLO@HIREALANTERN.EXAMPLE</span></div>
  </div>
</footer>

<div class="footer-bar">
  <p>All Rights Reserved, Copyrights @ 2016</p>
  <div class="pay-cards"><i></i><i></i><i></i></div>
</div>

</body>
</html>
```